Lawn care business card

I am looking for a quality designed personal business card to represent the quality and elegant nature of our company. We separate ourselves in our market by the aesthetic value of our work, so I am looking for marketing material that does the same. We target our marketing high end customers, and we try to avoid price shoppers. I am open to all design options, so long as they are in line with our companies values.

We are tend to go with a retro look on everything from our logo and print material, to our uniforms. We like to portray and "old fashion" set of core values, with a modern elegance. So a wild and crazy look is out of the question.

Things I'd like on the card:
1.) Logo
2.) Phone number: (816) 555-2931
3.) Website: Verdelynkc.com
4.) Email: robertfairley@verdelynkc.com
5.) My name: Robert Fairley
6.) Facebook link: facebook.com/VerdelynGardenandGrounds
7.) Instagram: http://instagram.com/verdelynkc

Attached is a copy of our logo.

Reason: More time is needed to gather conclusive feedback from the members of our marketing team.

```html
<!DOCTYPE html>
<html lang="en">
<head>
<meta charset="utf-8">
<title>Verdelyn – Business Card</title>
<link href="https://fonts.googleapis.com/css2?family=Arimo:wght@400;700&display=swap" rel="stylesheet">
<style>
  :root {
    --orange: #ef5a24;
    --ink: #1e1e1e;
    --paper: #ffffff;
    --backdrop: #e9e6e1;
    --badge: #232323;
  }
  html, body {
    margin: 0;
    width: 1200px;
    height: 800px;
    overflow: hidden;
    background: var(--backdrop);
    font-family: "Arimo", Arial, sans-serif;
  }
  .card {
    position: absolute;
    left: 75px;
    top: 100px;
    width: 1050px;
    height: 600px;
    background: var(--paper);
    overflow: hidden;
    box-shadow: 0 6px 24px rgba(0,0,0,0.18);
  }
  .card__band {
    position: absolute;
    left: 0;
    top: 0;
    width: 320px;
    height: 100%;
    background: var(--orange);
  }
  .brand {
    position: absolute;
    left: 230px;
    top: 80px;
    height: 180px;
    display: flex;
    align-items: center;
    gap: 28px;
  }
  .brand__dot {
    width: 180px;
    height: 180px;
    border-radius: 50%;
    background: var(--badge);
    flex: none;
  }
  .brand__name {
    font-size: 70px;
    font-weight: 700;
    color: var(--ink);
    letter-spacing: 2px;
    text-transform: uppercase;
  }
  .holder {
    position: absolute;
    left: 420px;
    top: 318px;
    width: 610px;
    margin: 0;
    font-size: 44px;
    font-weight: 400;
    letter-spacing: 3px;
    color: var(--ink);
    padding-bottom: 10px;
    border-bottom: 3px solid var(--orange);
  }
  .contacts {
    position: absolute;
    left: 360px;
    top: 400px;
    margin: 0;
    padding: 0;
    list-style: none;
  }
  .contacts__item {
    display: flex;
    align-items: center;
    gap: 16px;
    height: 36px;
    font-size: 26px;
    letter-spacing: 1.5px;
    color: var(--ink);
    white-space: nowrap;
  }
  .contacts__icon {
    width: 26px;
    height: 26px;
    flex: none;
    background: var(--orange);
    box-shadow: 4px -4px 0 var(--ink);
    display: flex;
    align-items: center;
    justify-content: center;
  }
  .contacts__icon svg {
    width: 18px;
    height: 18px;
  }
</style>
</head>
<body>
  <main class="card">
    <div class="card__band"></div>

    <div class="brand">
      <div class="brand__dot"></div>
      <span class="brand__name">Verdelyn</span>
    </div>

    <h1 class="holder">Robert Fairley</h1>

    <ul class="contacts">
      <li class="contacts__item">
        <span class="contacts__icon">
          <svg viewBox="0 0 24 24"><path d="M6.6 10.8c1.4 2.8 3.8 5.1 6.6 6.6l2.2-2.2c.3-.3.7-.4 1-.2 1.1.4 2.3.6 3.6.6.6 0 1 .4 1 1V20c0 .6-.4 1-1 1C10.6 21 3 13.4 3 4c0-.6.4-1 1-1h3.5c.6 0 1 .4 1 1 0 1.3.2 2.5.6 3.6.1.3 0 .7-.2 1l-2.3 2.2z" fill="#1e1e1e"/></svg>
        </span>
        (816) 555-2931
      </li>
      <li class="contacts__item">
        <span class="contacts__icon">
          <svg viewBox="0 0 24 24" fill="none" stroke="#1e1e1e" stroke-width="2"><circle cx="12" cy="12" r="9"/><path d="M3 12h18M12 3c3 3 3 15 0 18M12 3c-3 3-3 15 0 18"/></svg>
        </span>
        Verdelynkc.com
      </li>
      <li class="contacts__item">
        <span class="contacts__icon">
          <svg viewBox="0 0 24 24" fill="none" stroke="#1e1e1e" stroke-width="2"><rect x="3" y="6" width="18" height="12"/><path d="M3 6l9 7 9-7"/></svg>
        </span>
        robertfairley@verdelynkc.com
      </li>
      <li class="contacts__item">
        <span class="contacts__icon"></span>
        http://picturely.com/verdelynkc
      </li>
      <li class="contacts__item">
        <span class="contacts__icon"></span>
        friendlink.com/VerdelynGardenandGrounds
      </li>
    </ul>
  </main>
</body>
</html>
```